Vantrel System Web Page Design

This project is to design 6 pages of a web based medical system for clinics, hospitals, drugs suppliers, general items suppliers, insurance company, laboratories and patients (basically all parties which could be involved in).We want the designs of the browser, button, icon and layout are based on Zeltor, which is user friendly, looks professional, simple and neat but with powerful functions. We have uploaded few pictures of another system, please do not copy its design because this is not what we are looking for, the pictures are for you to know the elements should be included in our pages. Vantrel web-base system, design 6 pages1. Login PageShould include the following elements-company id with input field-login id with input field-password with input field2. Main Page (Navigation page)Should include the following elements-Appointment-Consultation-Patient-Drugs inventory -General supplies inventory -Laboratory-Suppliers-Insurance-Reports 3. Appointment PageShould include all the the elements in the respective pictures plus the followings-Daily View, Weekly View, Monthly View buttons4. Consultation PageShould include all the the elements in the respective picture5. Patient Page5.1 General information Should include all the the elements in the respective picture5.2 medical history/lab reportsShould include all the the elements in the respective picture plus the followings-Notify patient button-Share report button.
Updated on 28 Nov:
Please stop using Harbor Suite in your designs which is not the name of our system. We have just rename our system to Vantrel, please take note.
We need the system to look professional not playful, do not use too many colors and playful icons.

```html
<!DOCTYPE html>
<html lang="en">
<head>
<meta charset="utf-8">
<title>Vantrel System — Patient General Info</title>
<link href="https://fonts.googleapis.com/css2?family=Arimo:wght@400;700&display=swap" rel="stylesheet">
<style>
:root{
  --bg:#ececec;
  --panel:#ffffff;
  --sidebar:#e6e9ee;
  --sidebar-edge:#b9bec6;
  --title-top:#ebebeb;
  --title-bottom:#c9c9c9;
  --title-edge:#a5a5a5;
  --text:#2a2a2a;
  --muted:#777777;
  --heading:#7b828c;
  --line:#8e8e8e;
  --select-top:#6aa5e0;
  --select-bottom:#3f84cf;
  --btn-gray:#b5b5b5;
  --btn-blue-top:#6eaae6;
  --btn-blue-bottom:#3b82cf;
  --icon:#7d838b;
}
*{margin:0;padding:0;box-sizing:border-box}
html,body{width:1200px;height:675px;overflow:hidden;background:var(--bg);font-family:"Arimo",Helvetica,Arial,sans-serif;color:var(--text)}
.window{position:relative;width:1200px;height:675px;background:var(--bg)}
.titlebar{position:absolute;left:0;top:0;width:1200px;height:50px;background:linear-gradient(var(--title-top),var(--title-bottom));border-bottom:1px solid var(--title-edge)}
.light{position:absolute;top:5px;width:11px;height:11px;border-radius:50%;border:1px solid rgba(0,0,0,.25)}
.light.close{left:7px;background:radial-gradient(circle at 50% 35%,#ff8f85,#e0443a)}
.light.min{left:25px;background:radial-gradient(circle at 50% 35%,#ffe08a,#e0a528)}
.light.max{left:43px;background:radial-gradient(circle at 50% 35%,#9fe28a,#47a93a)}
.nav-buttons{position:absolute;left:9px;top:22px;width:45px;height:19px;border:1px solid #9a9a9a;border-radius:4px;background:linear-gradient(#fbfbfb,#dedede);display:flex}
.nav-buttons span{flex:1;display:flex;align-items:center;justify-content:center}
.nav-buttons span+span{border-left:1px solid #b0b0b0}
.window-title{position:absolute;left:0;right:0;top:20px;text-align:center;font-size:11.5px;color:#3b3b3b}
.search{position:absolute;left:1023px;top:22px;width:169px;height:19px;border:1px solid #9c9c9c;border-radius:10px;background:#fff}
.search svg{position:absolute}
.sidebar{position:absolute;left:0;top:51px;width:167px;height:624px;background:var(--sidebar);border-right:1px solid var(--sidebar-edge)}
.sidebar-heading{position:absolute;left:9px;top:31px;font-size:9.5px;letter-spacing:.8px;color:var(--heading);font-weight:700}
.nav-item{position:absolute;left:0;width:166px;height:21px;display:flex;align-items:center;font-size:12.8px;color:#1f1f1f}
.nav-item svg{position:absolute;left:9px;top:4px}
.nav-item .label{position:absolute;left:31px}
.nav-item.active{background:linear-gradient(var(--select-top),var(--select-bottom));color:#fff}
.panel{position:absolute;top:74px;width:455px;height:503px;background:var(--panel);border-radius:2px}
.panel.general{left:207px}
.panel.details{left:703px}
.label{font-size:11px;line-height:14px;color:var(--text)}
.panel .label{position:absolute;left:24.6px}
.value{position:absolute;font-size:11px;line-height:14px;color:var(--muted)}
.rule{position:absolute;left:109px;width:320px;height:1px;background:var(--line)}
.rule.short{width:272px}
.chevron{position:absolute;left:422px}
.radio{position:absolute;top:98px;width:12px;height:12px;border-radius:50%}
.radio.on{left:112px;background:radial-gradient(circle,#fff 0 2px,#2f7fd3 2.5px);border:1px solid #2a6fb8}
.radio.off{left:174px;background:linear-gradient(#fafafa,#e4e4e4);border:1px solid #c6c6c6}
.mini-btn{position:absolute;top:441px;width:17px;height:17px;background:#e9e9e9;border-radius:2px;font-size:12px;line-height:16px;text-align:center;color:#555}
.actions{position:absolute;left:207px;top:613px;display:flex;gap:19px}
.action{width:102px;height:27px;border-radius:2px;background:var(--btn-gray);color:#fff;font-size:11px;line-height:27px;text-align:center}
.action.primary{background:linear-gradient(var(--btn-blue-top),var(--btn-blue-bottom))}
</style>
</head>
<body>
<div class="window">
  <header class="titlebar">
    <span class="light close"></span><span class="light min"></span><span class="light max"></span>
    <div class="nav-buttons">
      <span><svg width="7" height="8"><path d="M6 0L0 4l6 4z" fill="#777"/></svg></span>
      <span><svg width="7" height="8"><path d="M1 0l6 4-6 4z" fill="#999"/></svg></span>
    </div>
    <div class="window-title">Vantrel System (Patient - General Info)</div>
    <div class="search">
      <svg style="left:6px;top:3px" width="12" height="12"><circle cx="5" cy="5" r="3.8" stroke="#555" stroke-width="1.5" fill="none"/><path d="M8 8l3 3" stroke="#555" stroke-width="1.6"/></svg>
      <svg style="left:153px;top:3px" width="12" height="12"><circle cx="6" cy="6" r="5.5" fill="#bdbdbd"/><path d="M4 4l4 4M8 4l-4 4" stroke="#fff" stroke-width="1.2"/></svg>
    </div>
  </header>

  <nav class="sidebar">
    <div class="sidebar-heading">IMPORTANT LINKS</div>
    <div class="nav-item" style="top:43px"><svg width="14" height="13"><g fill="var(--icon)"><circle cx="3" cy="2.5" r="2"/><circle cx="7" cy="2.5" r="2"/><circle cx="11" cy="2.5" r="2"/><rect x="1.5" y="5" width="3" height="8"/><rect x="5.5" y="5" width="3" height="8"/><rect x="9.5" y="5" width="3" height="8"/></g></svg><span class="label">Current Queue</span></div>
    <div class="nav-item" style="top:64px"><svg width="14" height="13"><rect x=".5" y="1.5" width="13" height="11" fill="none" stroke="var(--icon)"/><rect x=".5" y="1.5" width="13" height="3" fill="var(--icon)"/></svg><span class="label">Today Appointment</span></div>
    <div class="nav-item" style="top:85px"><svg width="14" height="13"><rect x=".5" y="1.5" width="13" height="11" fill="none" stroke="var(--icon)"/><rect x=".5" y="1.5" width="13" height="3" fill="var(--icon)"/><g fill="var(--icon)"><rect x="3" y="6" width="2" height="2"/><rect x="6" y="6" width="2" height="2"/><rect x="9" y="6" width="2" height="2"/><rect x="3" y="9" width="2" height="2"/><rect x="6" y="9" width="2" height="2"/></g></svg><span class="label">Appointment</span></div>
    <div class="nav-item active" style="top:106px"><svg width="14" height="13"><path d="M1 6.5Q7 0 13 6.5Q7 13 1 6.5z" fill="#fff"/><circle cx="7" cy="6.5" r="2" fill="#4a8cd4"/></svg><span class="label">Daily View</span></div>
    <div class="nav-item" style="top:127px"><svg width="14" height="13"><path d="M1 6.5Q7 0 13 6.5Q7 13 1 6.5z" fill="var(--icon)"/><circle cx="7" cy="6.5" r="2" fill="var(--sidebar)"/></svg><span class="label">Weekly View</span></div>
    <div class="nav-item" style="top:148px"><svg width="14" height="13"><path d="M1 6.5Q7 0 13 6.5Q7 13 1 6.5z" fill="var(--icon)"/><circle cx="7" cy="6.5" r="2" fill="var(--sidebar)"/></svg><span class="label">Monthly View</span></div>
    <div class="nav-item" style="top:169px"><svg width="14" height="13"><circle cx="7" cy="3.5" r="3" fill="none" stroke="var(--icon)" stroke-width="1.3"/><path d="M1.5 13q0-6 5.5-6t5.5 6z" fill="var(--icon)"/></svg><span class="label">New Patient</span></div>
    <div class="nav-item" style="top:190px"><svg width="14" height="13"><path d="M1 6Q6 0 12 5z" fill="var(--icon)"/><path d="M6.5 4l2 8" stroke="var(--icon)" stroke-width="1.2"/><path d="M1 12.5h12" stroke="var(--icon)"/></svg><span class="label">Public Holiday</span></div>
    <div class="nav-item" style="top:211px"><svg width="14" height="13"><path d="M2 2q-1 4 3 8t8 2l-2-3-2 1q-3-2-4-4l1-2z" fill="none" stroke="var(--icon)" stroke-width="1.2"/></svg><span class="label">Recall</span></div>
    <div class="nav-item" style="top:232px"><svg width="14" height="13"><g fill="var(--icon)"><rect x="2" y="1" width="2" height="9"/><rect x="7" y="3" width="2" height="7"/><rect x="1" y="11" width="12" height="2"/><circle cx="11" cy="6" r="2"/></g></svg><span class="label">Laboratory</span></div>
    <div class="nav-item" style="top:253px"><svg width="14" height="13"><rect x=".5" y="1.5" width="13" height="11" fill="none" stroke="var(--icon)"/><rect x=".5" y="1.5" width="13" height="3" fill="var(--icon)"/><path d="M5 7h4v4H5z" fill="none" stroke="var(--icon)"/></svg><span class="label">Appointment Reminder</span></div>
  </nav>

  <section class="panel general">
    <span class="label" style="top:40px">Patient Code:</span><i class="rule" style="top:51px"></i>
    <span class="label" style="top:67px">English Name:</span><i class="rule" style="top:77px"></i>
    <span class="label" style="top:93px">Chinese Name:</span><i class="rule" style="top:104px"></i>
    <span class="label" style="top:120px">H.K.I.D.:</span><i class="rule" style="top:130px"></i>
    <span class="label" style="top:146px">D.O.B.:</span><i class="rule" style="top:156px"></i>
    <span class="label" style="top:172px">Mobile No.:</span><i class="rule" style="top:183px"></i>
    <span class="label" style="top:199px">Res. Address:</span><i class="rule" style="top:227px"></i>
    <span class="label" style="top:243px">Res. District:</span><i class="rule" style="top:253px"></i>
    <svg class="chevron" style="top:243px" width="9" height="6"><path d="M1 1l3.5 3.5L8 1" stroke="#666" fill="none"/></svg>
    <span class="label" style="top:269px">Res. Area:</span><i class="rule" style="top:279px"></i>
    <svg class="chevron" style="top:269px" width="9" height="6"><path d="M1 1l3.5 3.5L8 1" stroke="#666" fill="none"/></svg>
    <span class="label" style="top:295px">Occupation:</span><i class="rule" style="top:307px"></i>
    <svg class="chevron" style="top:296px" width="9" height="6"><path d="M1 1l3.5 3.5L8 1" stroke="#666" fill="none"/></svg>
    <span class="label" style="top:322px">Contact:</span><i class="rule" style="top:332px"></i>
    <svg class="chevron" style="top:322px" width="9" height="6"><path d="M1 1l3.5 3.5L8 1" stroke="#666" fill="none"/></svg>
    <span class="label" style="top:348px">Insurance No.:</span><i class="rule" style="top:358px"></i>
    <span class="label" style="top:374px">Insurance Plan:</span><i class="rule" style="top:402px"></i>
    <span class="label" style="top:422px">Remarks:</span><i class="rule" style="top:459px"></i>
  </section>

  <section class="panel details">
    <span class="label" style="top:40px">No. of Records:</span><span class="value" style="left:130px;top:40px">4912</span>
    <span class="label" style="left:251px;top:40px;position:absolute">Last Modify Date:</span>
    <span class="label" style="top:67px">Last Patient Code:</span><span class="value" style="left:130px;top:67px">021010</span>
    <span class="label" style="top:98px">Gender:</span>
    <span class="radio on"></span><span class="value" style="left:127px;top:98px">Male</span>
    <span class="radio off"></span><span class="value" style="left:189px;top:98px">Female</span>
    <span class="label" style="top:128px">Prefix:</span><i class="rule" style="top:139px"></i>
    <svg class="chevron" style="top:128px" width="9" height="6"><path d="M1 1l3.5 3.5L8 1" stroke="#666" fill="none"/></svg>
    <span class="label" style="top:155px">Blood Type:</span><i class="rule" style="top:165px"></i>
    <svg class="chevron" style="top:155px" width="9" height="6"><path d="M1 1l3.5 3.5L8 1" stroke="#666" fill="none"/></svg>
    <span class="label" style="top:181px">Telephone:</span><i class="rule" style="top:191px"></i>
    <span class="label" style="top:207px">Bus. Address:</span><i class="rule" style="top:244px"></i>
    <span class="label" style="top:262px">Bus. District:</span><i class="rule" style="top:272px"></i>
    <svg class="chevron" style="top:262px" width="9" height="6"><path d="M1 1l3.5 3.5L8 1" stroke="#666" fill="none"/></svg>
    <span class="label" style="top:288px">Bus. Area:</span><i class="rule" style="top:299px"></i>
    <svg class="chevron" style="top:288px" width="9" height="6"><path d="M1 1l3.5 3.5L8 1" stroke="#666" fill="none"/></svg>
    <span class="label" style="top:315px">Dr. In Charge:</span><i class="rule" style="top:325px"></i>
    <svg class="chevron" style="top:315px" width="9" height="6"><path d="M1 1l3.5 3.5L8 1" stroke="#666" fill="none"/></svg>
    <span class="label" style="top:341px">Referred By:</span><i class="rule" style="top:351px"></i>
    <svg class="chevron" style="top:341px" width="9" height="6"><path d="M1 1l3.5 3.5L8 1" stroke="#666" fill="none"/></svg>
    <span class="label" style="top:367px">Email:</span><i class="rule" style="top:378px"></i>
    <span class="label" style="top:395px">Family History:</span><i class="rule" style="top:432px"></i>
    <span class="label" style="top:448px">Group:</span><i class="rule short" style="top:459px"></i>
    <svg class="chevron" style="left:374px;top:448px" width="9" height="6"><path d="M1 1l3.5 3.5L8 1" stroke="#666" fill="none"/></svg>
    <span class="mini-btn" style="left:387px">+</span><span class="mini-btn" style="left:410px">-</span>
  </section>

  <div class="actions">
    <span class="action primary">New</span>
    <span class="action">Save</span>
    <span class="action">Print Eng.</span>
    <span class="action">Print Chi.</span>
    <span class="action">Patient Chart</span>
    <span class="action">Main</span>
  </div>
</div>
</body>
</html>
```